Plate of the Raven: Half-Page Magazine Ad

advertisement in a travel magazine for a casual/fine dining restaurant in the heart of Whitehorse, Yukon
Needs to say that it is located in the Stonefield Hotel, 247 Larch Avenue.

Northern inspired cuisine
plateoftheraven.example

Don't need to use all the pictures

Dimensions: ad is a half-page, dimensions are 7.25" x 4.8".

Target Market(s)

Upscale dining, corporate travellers

Industry/Entity Type

Restaurant

Colors
0054AA
0677BA
7BADD7
CADEEF
E8F1F8
0094D4
00A9DD
6FCCEA
C7EBF8
E9F6FB
00AB8E
00BBA5
67D7C9
C6EFE9
E9F9F6

Requirements
Must have
• Restaurant logo
Nice to have
• Simple, clean design with upscale feel

```html
<!DOCTYPE html>
<html lang="en">
<head>
<meta charset="utf-8">
<title>Plate of the Raven – Half-Page Ad</title>
<link href="https://fonts.googleapis.com/css2?family=Montserrat:wght@400;500;600&display=swap" rel="stylesheet">
<style>
  :root {
    --page-bg: #bdbdbf;
    --ad-bg: #ebebed;
    --ink: #111114;
    --line: #2a2a2e;
    --ring: #cfcfd2;
    --white: #ffffff;
  }
  * { margin: 0; padding: 0; box-sizing: border-box; }
  html, body { width: 1200px; height: 2340px; overflow: hidden; }
  body {
    background: var(--page-bg);
    font-family: "Montserrat", sans-serif;
    color: var(--ink);
    position: relative;
  }
  .ad-wrap {
    position: absolute;
    left: 50px;
    top: 458px;
    width: 1100px;
    height: 1424px;
  }
  .ad {
    position: absolute;
    left: 0; top: 0;
    width: 1026px;
    height: 1328px;
    transform: scale(1.0721);
    transform-origin: 0 0;
    background: var(--ad-bg);
    box-shadow: 0 6px 18px rgba(0,0,0,0.18);
    overflow: hidden;
  }
  .ad-art { position: absolute; left: 0; top: 0; width: 1026px; height: 1328px; }

  .brand-mark {
    position: absolute;
    left: 272px; top: 895px;
    width: 190px;
    font-weight: 600;
    font-size: 44px;
    line-height: 1.02;
    text-transform: uppercase;
    text-align: right;
    color: var(--ink);
  }
  .headline {
    position: absolute;
    left: 573px; top: 884px;
    font-weight: 600;
    font-size: 44px;
    line-height: 1.06;
    white-space: nowrap;
  }
  .intro {
    position: absolute;
    left: 573px; top: 994px;
    font-size: 17.5px;
    line-height: 1.2;
    white-space: nowrap;
  }
  .features {
    position: absolute;
    left: 573px; top: 1124px;
    list-style: none;
    font-weight: 500;
    font-size: 17.5px;
    line-height: 30px;
    white-space: nowrap;
  }
  .features li { display: flex; align-items: center; gap: 12px; }
  .features svg { width: 18px; height: 18px; flex: none; }

  .pill {
    position: absolute;
    height: 46px;
    border: 1.5px solid var(--line);
    border-radius: 23px;
    display: flex;
    align-items: center;
    gap: 14px;
    padding-left: 4px;
    font-size: 16.5px;
    letter-spacing: 0.3px;
    white-space: nowrap;
  }
  .pill .pill-icon {
    width: 36px; height: 36px;
    border-radius: 50%;
    background: var(--ink);
    display: flex; align-items: center; justify-content: center;
    flex: none;
  }
  .pill-web { left: 60px; top: 1222px; width: 392px; }
  .pill-address { left: 573px; top: 1222px; width: 392px; }
</style>
</head>
<body>
  <div class="ad-wrap">
    <div class="ad">
      <svg class="ad-art" viewBox="0 0 1026 1328" xmlns="http://www.w3.org/2000/svg">
        <defs>
          <linearGradient id="interior-tone" x1="0" y1="0" x2="1" y2="1">
            <stop offset="0" stop-color="#4a3a30"/>
            <stop offset="0.35" stop-color="#8d8a78"/>
            <stop offset="0.6" stop-color="#3d4250"/>
            <stop offset="1" stop-color="#1f1c1e"/>
          </linearGradient>
          <radialGradient id="dish-charcuterie"><stop offset="0" stop-color="#e6c25a"/><stop offset="1" stop-color="#8e2f32"/></radialGradient>
          <radialGradient id="dish-salad"><stop offset="0" stop-color="#e8b04a"/><stop offset="1" stop-color="#7a3a4a"/></radialGradient>
          <radialGradient id="dish-scallops"><stop offset="0" stop-color="#e9d6a4"/><stop offset="1" stop-color="#8a5a2c"/></radialGradient>
          <radialGradient id="dish-steak"><stop offset="0" stop-color="#efe6cf"/><stop offset="1" stop-color="#8c5a4a"/></radialGradient>
          <linearGradient id="raven-sketch" x1="0" y1="0" x2="1" y2="1">
            <stop offset="0" stop-color="#d4d4d6"/>
            <stop offset="1" stop-color="#9c9ca0"/>
          </linearGradient>
        </defs>

        <path role="img" aria-label="Photo of the restaurant bar interior with stools and shelves of glasses"
              fill="url(#interior-tone)"
              d="M0,0 H1026 V640 C1026,760 960,835 860,832 C760,830 700,760 620,700 C540,640 470,545 330,505 C240,480 140,490 80,560 C40,605 10,650 0,690 Z"/>
        <path fill="none" stroke="var(--white)" stroke-width="10"
              d="M1026,640 C1026,760 960,835 860,832 C760,830 700,760 620,700 C540,640 470,545 330,505 C240,480 140,490 80,560 C40,605 10,650 0,690"/>

        <path fill="none" stroke="#f2f2f2" stroke-opacity="0.8" stroke-width="1"
              d="M60,540 V80 Q60,60 80,60 H945 Q965,60 965,80 V540"/>

        <g class="dish-row">
          <circle cx="168" cy="665" r="118" fill="var(--ring)"/>
          <circle role="img" aria-label="Photo of a charcuterie and cheese board" cx="168" cy="665" r="107" fill="url(#dish-charcuterie)"/>
          <circle cx="398" cy="665" r="118" fill="var(--ring)"/>
          <circle role="img" aria-label="Photo of crab, soup and a colourful salad" cx="398" cy="665" r="107" fill="url(#dish-salad)"/>
          <circle cx="628" cy="665" r="118" fill="var(--ring)"/>
          <circle role="img" aria-label="Photo of seared scallops in cream sauce" cx="628" cy="665" r="107" fill="url(#dish-scallops)"/>
          <circle cx="858" cy="665" r="118" fill="var(--ring)"/>
          <circle role="img" aria-label="Photo of sliced meat with potatoes and greens" cx="858" cy="665" r="107" fill="url(#dish-steak)"/>
        </g>

        <g stroke="var(--line)" stroke-width="1">
          <line x1="60" y1="785" x2="60" y2="1245"/>
          <line x1="513" y1="785" x2="513" y2="1268"/>
          <line x1="470" y1="1268" x2="557" y2="1268"/>
          <line x1="965" y1="800" x2="965" y2="1245"/>
          <line x1="573" y1="1098" x2="940" y2="1098"/>
        </g>

        <rect role="img" aria-label="Pencil sketch illustration of a raven" x="60" y="840" width="205" height="340" rx="4" fill="url(#raven-sketch)" opacity="0.8"/>
      </svg>

      <div class="brand-mark">Plate of the Raven</div>

      <h1 class="headline">The Plate Of<br>The Raven</h1>
      <p class="intro">Elegant comfort food that is upscale<br>but simple. Paired with an impressive<br>wine selection and a modern spin on<br>classic cocktails.</p>

      <ul class="features">
        <li><svg viewBox="0 0 18 18"><circle cx="9" cy="9" r="8" fill="none" stroke="#111" stroke-width="1.4"/><path d="M5.3 9.2 L8 11.6 L12.8 6.6" fill="none" stroke="#111" stroke-width="1.4"/></svg>Open evenings with a summer patio</li>
        <li><svg viewBox="0 0 18 18"><circle cx="9" cy="9" r="8" fill="none" stroke="#111" stroke-width="1.4"/><path d="M5.3 9.2 L8 11.6 L12.8 6.6" fill="none" stroke="#111" stroke-width="1.4"/></svg>Northern inspired cuisine</li>
      </ul>

      <div class="pill pill-web">
        <span class="pill-icon"><svg width="22" height="22" viewBox="0 0 22 22"><g fill="none" stroke="#fff" stroke-width="1.5"><circle cx="11" cy="11" r="9"/><ellipse cx="11" cy="11" rx="4" ry="9"/><line x1="2" y1="11" x2="20" y2="11"/></g></svg></span>
        <span>www.plateoftheraven.example</span>
      </div>

      <div class="pill pill-address">
        <span class="pill-icon"><svg width="20" height="22" viewBox="0 0 20 22"><path d="M10 2 C5.6 2 3 5 3 8.6 C3 13 10 20 10 20 C10 20 17 13 17 8.6 C17 5 14.4 2 10 2 Z" fill="none" stroke="#fff" stroke-width="1.6"/><circle cx="10" cy="8.6" r="2.4" fill="none" stroke="#fff" stroke-width="1.6"/></svg></span>
        <span>Stonefield Hotel, 247 Larch Avenue</span>
      </div>
    </div>
  </div>
</body>
</html>
```